Stylish Business Cards Wanted

- DOUBLE SIDED Design Required -

High end, edgy cards for a corporate and personal stylist. Must include logo,
Name: Belinda Harwick
Title: Director and Stylist
telephone : +61 8 7142 5809
email: belinda@theloombriefing.example
website: theloombriefing.example
Tag: Corporate Workwear & Uniform Specialist | Personal Stylist
Would like nice icons for telephone, email, website

Target Market(s)

Businesses wanting stylish uniforms, people wanting stylish wardrobes

Industry/Entity Type

Corporate Workwear Stylist

Contact Information for Business Card

I would like black, white and gold foiling incorporated in the design - possibly a touch of the other colours on my branding guide attached Name: Belinda Harwick Title: Director and Stylist telephone : +61 8 7142 5809 email: belinda@theloombriefing.example website: theloombriefing.example Tag: Corporate Workwear & Uniform Specialist | Personal Stylist Would like nice icons for telephone, email, website

Font styles to use
Other font styles liked:
• Raleway

Colors

Designer to choose colors to be used in the design.

Requirements
Must have
• Gold foil accents

```html
<!DOCTYPE html>
<html lang="en">
<head>
<meta charset="utf-8">
<title>The Loom Briefing – Business Card</title>
<link rel="stylesheet" href="https://fonts.googleapis.com/css2?family=Raleway:wght@400;500;700&family=Montserrat:wght@400;500;700&display=swap">
<style>
  :root {
    --backdrop: #1c1c1c;
    --card-black: #231f20;
    --emboss: #0b0a0a;
    --white: #ffffff;
    --gold: #e2b64f;
    --ink: #141213;
  }
  * { box-sizing: border-box; margin: 0; padding: 0; }
  html, body { width: 1200px; height: 1015px; overflow: hidden; }
  body {
    background: var(--backdrop);
    font-family: "Raleway", sans-serif;
    position: relative;
  }
  .card {
    position: absolute;
    left: 220px;
    width: 760px;
    height: 434px;
    background: var(--card-black);
    overflow: hidden;
    box-shadow: 0 12px 30px rgba(0,0,0,.45);
  }
  .card--back { top: 52px; }
  .card--front { top: 530px; }

  /* Back side */
  .back-wordmark {
    position: absolute;
    left: 0; right: 0; top: 120px;
    text-align: center;
    color: var(--emboss);
    font-weight: 700;
    font-size: 64px;
    letter-spacing: 1px;
  }
  .back-tagline {
    position: absolute;
    left: 0; right: 0; bottom: 60px;
    text-align: center;
    color: var(--white);
    font-family: "Montserrat", sans-serif;
    font-size: 21px;
    letter-spacing: .5px;
  }
  .back-tagline .divider {
    display: inline-block;
    width: 8px; height: 8px;
    border-radius: 50%;
    background: var(--gold);
    vertical-align: middle;
    margin: 0 14px;
  }

  /* Front side */
  .front-disc { position: absolute; inset: 0; }
  .front-wordmark {
    position: absolute;
    left: 520px; top: 98px;
    width: 260px;
    color: var(--ink);
    font-weight: 700;
    font-size: 38px;
    line-height: 1.1;
    text-align: center;
  }
  .holder {
    position: absolute;
    left: 56px; top: 78px;
  }
  .holder-name {
    color: var(--gold);
    font-weight: 700;
    font-size: 30px;
    letter-spacing: .5px;
    text-transform: uppercase;
  }
  .holder-title {
    color: var(--white);
    font-family: "Montserrat", sans-serif;
    font-size: 21px;
    margin-top: 4px;
  }
  .contacts {
    position: absolute;
    left: 56px; bottom: 46px;
    list-style: none;
  }
  .contact {
    display: flex;
    align-items: center;
    gap: 14px;
    color: var(--white);
    font-family: "Montserrat", sans-serif;
    font-size: 20px;
    line-height: 34px;
    white-space: nowrap;
  }
  .contact svg { width: 22px; height: 22px; flex: none; }
</style>
</head>
<body>

<section class="card card--back" aria-label="Business card, back">
  <div class="back-wordmark">The Loom Briefing</div>
  <p class="back-tagline">Corporate Workwear &amp; Uniform Specialist<span class="divider"></span>Personal Stylist</p>
</section>

<section class="card card--front" aria-label="Business card, front">
  <svg class="front-disc" viewBox="0 0 760 434" aria-hidden="true">
    <circle cx="640" cy="140" r="240" fill="var(--white)"/>
    <path d="M441 40 A228 228 0 0 0 628 363" fill="none" stroke="var(--gold)" stroke-width="6" stroke-linecap="round"/>
  </svg>
  <div class="front-wordmark">The Loom Briefing</div>

  <div class="holder">
    <h1 class="holder-name">Belinda Harwick</h1>
    <p class="holder-title">Director and Stylist</p>
  </div>

  <ul class="contacts">
    <li class="contact">
      <svg viewBox="0 0 24 24" fill="var(--gold)" aria-hidden="true"><path d="M6.6 10.8a15.1 15.1 0 0 0 6.6 6.6l2.2-2.2a1 1 0 0 1 1-.25 11.4 11.4 0 0 0 3.6.57 1 1 0 0 1 1 1V20a1 1 0 0 1-1 1A17 17 0 0 1 3 4a1 1 0 0 1 1-1h3.5a1 1 0 0 1 1 1c0 1.25.2 2.45.57 3.6a1 1 0 0 1-.25 1z"/></svg>
      +61 8 7142 5809
    </li>
    <li class="contact">
      <svg viewBox="0 0 24 24" fill="none" stroke="var(--gold)" stroke-width="2" aria-hidden="true"><circle cx="12" cy="12" r="9.5"/><ellipse cx="12" cy="12" rx="4" ry="9.5"/><path d="M2.5 12h19M4 7h16M4 17h16"/></svg>
      theloombriefing.example
    </li>
    <li class="contact">
      <svg viewBox="0 0 24 24" aria-hidden="true"><rect x="2" y="5" width="20" height="14" fill="var(--gold)"/><path d="M2 5l10 8 10-8" fill="none" stroke="var(--card-black)" stroke-width="1.6"/></svg>
      belinda@theloombriefing.example
    </li>
  </ul>
</section>

</body>
</html>
```